Design and Renovation Company Luxury Business Card

I want to create a luxury business card for a Design and Renovation Firm . We will use our current logo. The company name is 528BUILDA. We do not want anything standard. We need a very unique concept.
Please see uploaded inspiration. I really like the textured paper option. I would like the card to be thick with debossing, and/or embossing options. The logo has orange in it but I would like to see the card with and without the orange. I think the orange may make the company feel less high-end. The goal is to elevate the logo not match its vibe per se of the logo. We want something very unique, not standard at all!
I would like a space for :
Logo,
Name,
Position,
Email,
Office number,
Website Address,
Business Address,
Thank you!
Have fun!
Target Market(s)
Home owners Age 35 +
Industry/Entity Type
Design and Renovation
Contact Information for Business Card
Logo, Name, Position, Email, Office number, Website Address, Business Address,.
Colors
Designer to choose colors to be used in the design.
Requirements
Must have
- A luxury designer feel. Must be black or dark grey but open to other luxury ideas.
Nice to have
- Gold, silver, black embossing or debossing. Textured paper design.
Should not have
- A cheap look and feel.

```html
<!DOCTYPE html>
<html lang="en">
<head>
<meta charset="utf-8">
<title>528BUILDA Business Card</title>
<link href="https://fonts.googleapis.com/css2?family=Roboto:wght@400;500&display=swap" rel="stylesheet">
<style>
  :root {
    --stage: #1c1c1e;
    --card-top: #343434;
    --card-bottom: #262626;
    --orange: #f29422;
    --orange-edge: #e8890f;
    --white: #f4f4f4;
    --muted: #d9d9d9;
    --icon-cut: #2c2c2c;
  }
  * { box-sizing: border-box; margin: 0; padding: 0; }
  html, body { width: 1200px; height: 840px; overflow: hidden; }
  body {
    background: var(--stage);
    font-family: "Roboto", Arial, sans-serif;
    display: flex;
    align-items: center;
    justify-content: center;
    gap: 40px;
  }
  .card {
    position: relative;
    width: 540px;
    height: 310px;
    border-radius: 24px;
    background: linear-gradient(160deg, var(--card-top), var(--card-bottom));
    box-shadow: 0 5px 0 var(--orange-edge), 0 18px 30px rgba(0,0,0,.45);
    overflow: hidden;
    color: var(--white);
  }

  /* Company name block */
  .company { display: flex; flex-direction: column; }
  .company__name {
    font-weight: 500; font-size: 50px; line-height: 1; color: var(--white);
  }
  .company__tagline {
    font-weight: 400; font-size: 13px; color: var(--muted); margin-top: 8px;
  }

  /* Front */
  .card--front { display: flex; align-items: center; justify-content: center; }

  /* Back */
  .corner-tab {
    position: absolute; top: 0; right: 44px; width: 22px; height: 34px; background: var(--orange);
  }
  .person { position: absolute; top: 26px; right: 76px; text-align: right; }
  .person__name { color: var(--orange); font-weight: 500; font-size: 20px; letter-spacing: .3px; }
  .person__role { color: var(--white); font-size: 14px; margin-top: 2px; }

  .card--back .company { position: absolute; left: 36px; top: 92px; }
  .card--back .company__name { font-size: 44px; }
  .card--back .company__tagline { font-size: 12px; margin-top: 6px; }

  .address {
    position: absolute; left: 80px; top: 190px; font-size: 15px; line-height: 1.3; color: var(--muted);
  }
  .contact-list {
    position: absolute; left: 64px; top: 238px; list-style: none;
    font-size: 15px; line-height: 1.3; color: var(--muted);
  }
  .contact-list li { display: flex; align-items: center; gap: 6px; }
  .contact-list svg { width: 12px; height: 12px; flex: none; }
</style>
</head>
<body>

  <section class="card card--front" aria-label="Card front">
    <div class="company">
      <span class="company__name">528BUILDA</span>
      <span class="company__tagline">Design and Renovation Firm</span>
    </div>
  </section>

  <section class="card card--back" aria-label="Card back">
    <span class="corner-tab"></span>
    <div class="person">
      <p class="person__name">DANIEL MERCER</p>
      <p class="person__role">Manager</p>
    </div>

    <div class="company">
      <span class="company__name">528BUILDA</span>
      <span class="company__tagline">Design and Renovation Firm</span>
    </div>

    <p class="address">Your Address, City<br>State, Zip 0000</p>

    <ul class="contact-list">
      <li>
        <svg viewBox="0 0 12 12" aria-hidden="true"><path fill="var(--orange)" d="M1 4c0-2 2-3 5-3s5 1 5 3l-2 1-1-1.5H4L3 5 1 4zm2 2h6l1 5H2l1-5z"/></svg>
        123-456-2100
      </li>
      <li>
        <svg viewBox="0 0 12 12" aria-hidden="true"><rect x="1" y="3" width="10" height="7" fill="var(--orange)"/><path d="M1 3l5 4 5-4" stroke="var(--icon-cut)" stroke-width="1" fill="none"/></svg>
        youremail@mailbox.com
      </li>
      <li>
        <svg viewBox="0 0 12 12" aria-hidden="true"><circle cx="6" cy="6" r="5" fill="var(--orange)"/><path d="M1 6h10M6 1c-2 2.5-2 7.5 0 10M6 1c2 2.5 2 7.5 0 10" stroke="var(--icon-cut)" stroke-width=".8" fill="none"/></svg>
        www.yourwebsite.com
      </li>
    </ul>
  </section>

</body>
</html>
```